Mayhon online ordering platform looking for a great web design

Mayhon - from the Vietnamese words Mây Hồng meaning financial success.
Background
Mayhon is an online ordering platform for small retail businesses (corner stores). The idea is that small retailers will use the website to order their supplies. From this we will utilise the group buying to get better deals for them that they could not achieve individually.
We are looking for a simple but stylish design for our ordering page. The layout needs to be efficient, logical and self explanatory.
Products to be sold on the site are FMCG (fast moving consumer goods). Potential to be 000's of items.
Considerations
- end users are not technologically adept.
- Users are generally older so small print will not be well received.
- Use of touch screen monitors to select/change items so spacing in design is vital.
- Logical display of category and sub-categories.
- Easy selection of products to order as well as modification of quantity.
- Shopping cart with easy change of item quantity.
- List of items for ordering can be paginated.
- Items listed will have image for easy identification.
- Search box
- Format should be in psd (photoshop) or complete html/css
- All this information needs to be displayed on the one page.
Product information to contain the following:
- Image
- Price
- Product name
- Size
Area for prominent display of specials without crowding the product information.

```html
<!DOCTYPE html>
<html lang="en">
<head>
<meta charset="utf-8">
<title>Mayhon – Sub Category</title>
<link href="https://fonts.googleapis.com/css2?family=Ubuntu:wght@400;500;700&display=swap" rel="stylesheet">
<style>
:root{
  --orange:#f05a28;
  --orange-dark:#d9461a;
  --ink:#3d3d3d;
  --muted:#6b6b6b;
  --bar:#0e0e0e;
  --band:#f4f1e6;
  --band-line:#d9d4c2;
  --panel-line:#dcdcdc;
  --teal:#0bbec6;
  --white:#ffffff;
}
*{box-sizing:border-box;margin:0;padding:0}
html,body{width:960px;height:1200px;overflow:hidden;background:var(--white);font-family:"Ubuntu",sans-serif;color:var(--ink)}
body{position:relative}
.topbar{height:27px;background:var(--bar);display:flex;justify-content:flex-end;align-items:center;gap:21px;padding-right:106px;font-size:10px;font-weight:500;color:var(--white)}
.brand{position:absolute;left:102px;top:54px;font-size:27px;color:#8f8f8f;font-weight:400;letter-spacing:.5px;display:flex;align-items:center;gap:8px}
.brand-dot{width:12px;height:12px;background:var(--orange)}
.main-nav{position:absolute;left:103px;top:108px;width:753px;height:27px;background:var(--band);border:1px solid var(--band-line);display:flex;align-items:center;font-size:11px}
.main-nav a{color:var(--ink);text-decoration:none;padding:0 24px;border-right:1px solid var(--band-line);line-height:17px}
.main-nav a.active{background:var(--orange);color:var(--white);font-weight:700;font-size:12px;line-height:27px;height:27px;margin-top:-1px;padding:0 22px;width:79px;text-align:center;border:none;margin-right:6px}
.search{margin-left:auto;margin-right:2px;width:170px;height:20px;border:1px solid var(--band-line);background:var(--white);font-size:10px;font-style:italic;color:#777;padding:3px 8px}
.banner{position:absolute;left:104px;top:140px;width:752px;height:154px;border:1px solid var(--panel-line);padding:4px}
.banner-inner{position:relative;width:100%;height:100%;background:var(--teal);overflow:hidden}
.banner-photo{position:absolute;left:0;top:0;width:250px;height:100%;background:linear-gradient(90deg,#d6c6b8 0%,#e8e2dc 55%,#c8302e 75%,var(--teal) 100%)}
.offer{position:absolute;left:255px;top:24px;display:flex;align-items:center;color:var(--white);font-weight:700}
.offer-up{writing-mode:vertical-rl;transform:rotate(180deg);font-size:22px;letter-spacing:1px;margin-right:4px}
.offer-big{font-size:84px;letter-spacing:-2px;line-height:1;transform:scaleX(.8);transform-origin:left}
.learn{position:absolute;right:5px;bottom:5px;background:#f4f1e6;border:1px solid #cfc9b6;font-size:10px;padding:5px 8px;color:var(--ink)}
.cat-row{position:absolute;left:103px;width:753px;height:27px;background:var(--band);border:1px solid var(--band-line);display:flex;align-items:center;font-size:11px;padding-left:4px}
.cat-row span{padding:0 8px;border-right:1px solid var(--band-line);line-height:15px}
.cat-row span.active{background:var(--orange);color:var(--white);font-weight:700;font-size:12px;line-height:27px;height:27px;border:1px solid var(--orange-dark)}
.row-main{top:300px}
.row-sub{top:330px}
.crumbs{position:absolute;left:105px;top:368px;font-size:9px;color:var(--ink)}
.crumbs em{font-style:normal;color:var(--orange)}
.page-title{position:absolute;left:105px;top:381px;font-size:22px;font-weight:500;color:var(--orange)}
.panel{position:absolute;left:104px;width:752px;border:1px solid var(--panel-line);padding:0 13px 0 8px;overflow:hidden}
.panel-featured{top:416px;height:228px}
.panel-latest{top:649px;height:551px;border-bottom:none}
.panel h2{font-size:15px;font-weight:400;color:var(--orange);padding:8px 0 7px 0;border-bottom:1px solid var(--panel-line)}
.panel h2 small{font-size:9px;color:var(--muted)}
.grid{display:grid;grid-template-columns:135px repeat(4,150px);border-bottom:1px solid var(--panel-line);padding:10px 0 6px}
.grid:last-child{border-bottom:none}
.card{border-left:1px solid var(--panel-line);padding:0 10px 0 20px}
.card:first-child{border-left:none;padding-left:14px}
.shot{height:137px;display:flex;justify-content:center;align-items:flex-start;padding-top:2px}
.bottle{width:48px;height:132px;border-radius:14px 14px 8px 8px}
.green{background:linear-gradient(90deg,#2f9d2a,#56cc44 50%,#2f9d2a)}
.blue{background:linear-gradient(180deg,#1d4fa8 0 22%,#f4f6fa 22%);width:44px}
.white{background:linear-gradient(90deg,#d9dcdf,#ffffff 50%,#d9dcdf);width:54px}
.pink{background:linear-gradient(90deg,#c1174a,#ec3a6e 50%,#c1174a);width:36px;height:124px}
.name{font-size:10.5px;font-weight:500;color:var(--orange);margin-top:9px}
.meta{display:flex;justify-content:space-between;font-size:10px;color:var(--ink);margin-top:4px}
</style>
</head>
<body>
<header class="topbar"><span>Register</span><span>Sign Up</span><span>My Cart (2)</span></header>
<div class="brand"><span class="brand-dot"></span>Mayhon</div>
<nav class="main-nav">
  <a class="active">Home</a><a>About</a><a>Categories</a><a>How it works</a><a>Contact Us</a><a>Support</a>
  <div class="search">search</div>
</nav>
<section class="banner">
  <div class="banner-inner">
    <div class="banner-photo" role="img" aria-label="Photo of a shopper in a white top with a red bag strap"></div>
    <div class="offer"><span class="offer-up">UPTO</span><span class="offer-big">20% OFF</span></div>
    <div class="learn">Learn More</div>
  </div>
</section>
<div class="cat-row row-main"><span>Lorem</span><span>Ipsum</span><span>Proin</span><span>Gravida</span><span class="active">Main Category</span><span>Nibhvel</span><span>Auctor</span><span>Aliquet</span><span>Aenean</span></div>
<div class="cat-row row-sub"><span>Ipsum</span><span>Nec sagittis</span><span>Sem nibh id</span><span>Duis sed</span><span>Odio sit</span><span>Amet nibh</span><span class="active">Sub Category</span><span>Vulputate</span><span>Cursus</span><span>Amet</span></div>
<div class="crumbs">Home &gt; Main Category &gt; <em>Sub Category</em></div>
<h1 class="page-title">Sub Category</h1>

<section class="panel panel-featured">
  <h2>Featured Products</h2>
  <div class="grid">
    <div class="card"><div class="shot"><div class="bottle green" role="img" aria-label="Green shampoo bottle"></div></div><div class="name">Product Name</div><div class="meta"><span>500ml</span><span>$2.59</span></div></div>
    <div class="card"><div class="shot"><div class="bottle blue" role="img" aria-label="Blue and white shampoo bottle"></div></div><div class="name">Product Name</div><div class="meta"><span>500ml</span><span>$2.59</span></div></div>
    <div class="card"><div class="shot"><div class="bottle white" role="img" aria-label="White shampoo bottle"></div></div><div class="name">Product Name</div><div class="meta"><span>500ml</span><span>$2.59</span></div></div>
    <div class="card"><div class="shot"><div class="bottle white" role="img" aria-label="White shampoo bottle"></div></div><div class="name">Product Name</div><div class="meta"><span>500ml</span><span>$2.59</span></div></div>
    <div class="card"><div class="shot"><div class="bottle pink" role="img" aria-label="Pink shampoo bottle"></div></div><div class="name">Product Name</div><div class="meta"><span>500ml</span><span>$2.59</span></div></div>
  </div>
</section>

<section class="panel panel-latest">
  <h2>Latest Arrivals <small>(see all)</small></h2>
  <div class="grid">
    <div class="card"><div class="shot"><div class="bottle green" role="img" aria-label="Green shampoo bottle"></div></div><div class="name">Product Name</div><div class="meta"><span>500ml</span><span>$2.59</span></div></div>
    <div class="card"><div class="shot"><div class="bottle blue" role="img" aria-label="Blue and white shampoo bottle"></div></div><div class="name">Product Name</div><div class="meta"><span>500ml</span><span>$2.59</span></div></div>
    <div class="card"><div class="shot"><div class="bottle white" role="img" aria-label="White shampoo bottle"></div></div><div class="name">Product Name</div><div class="meta"><span>500ml</span><span>$2.59</span></div></div>
    <div class="card"><div class="shot"><div class="bottle white" role="img" aria-label="White shampoo bottle"></div></div><div class="name">Product Name</div><div class="meta"><span>500ml</span><span>$2.59</span></div></div>
    <div class="card"><div class="shot"><div class="bottle pink" role="img" aria-label="Pink shampoo bottle"></div></div><div class="name">Product Name</div><div class="meta"><span>500ml</span><span>$2.59</span></div></div>
  </div>
  <div class="grid">
    <div class="card"><div class="shot"><div class="bottle green" role="img" aria-label="Green shampoo bottle"></div></div><div class="name">Product Name</div><div class="meta"><span>500ml</span><span>$2.59</span></div></div>
    <div class="card"><div class="shot"><div class="bottle blue" role="img" aria-label="Blue and white shampoo bottle"></div></div><div class="name">Product Name</div><div class="meta"><span>500ml</span><span>$2.59</span></div></div>
    <div class="card"><div class="shot"><div class="bottle white" role="img" aria-label="White shampoo bottle"></div></div><div class="name">Product Name</div><div class="meta"><span>500ml</span><span>$2.59</span></div></div>
    <div class="card"><div class="shot"><div class="bottle white" role="img" aria-label="White shampoo bottle"></div></div><div class="name">Product Name</div><div class="meta"><span>500ml</span><span>$2.59</span></div></div>
    <div class="card"><div class="shot"><div class="bottle pink" role="img" aria-label="Pink shampoo bottle"></div></div><div class="name">Product Name</div><div class="meta"><span>500ml</span><span>$2.59</span></div></div>
  </div>
  <div class="grid">
    <div class="card"><div class="shot"><div class="bottle green" role="img" aria-label="Green shampoo bottle"></div></div></div>
    <div class="card"><div class="shot"><div class="bottle blue" role="img" aria-label="Blue and white shampoo bottle"></div></div></div>
    <div class="card"><div class="shot"><div class="bottle white" role="img" aria-label="White shampoo bottle"></div></div></div>
    <div class="card"><div class="shot"><div class="bottle white" role="img" aria-label="White shampoo bottle"></div></div></div>
    <div class="card"><div class="shot"><div class="bottle pink" role="img" aria-label="Pink shampoo bottle"></div></div></div>
  </div>
</section>
</body>
</html>
```